Consulting company business cards

We have a base design, but would be willing to update. We have a new logo/"tag" that needs to be added. Current business card design is attached for reference into our "style."

Industry/Entity Type

Business

Contact Information for Business Card

Should contain name and title, office number, mobile number if appropriate, e-mail, website, physical address, and company logo.

Font styles to use
Other font styles liked:
• See current card design on KorvandBCard

Colors
0455a3
85acd3
aaaaaa

Requirements
Must have
• Our colors are navy blue, gray, and a lighter blue
Nice to have
• Design that I can easily drop in new names/titles as we hire employees.

```html
<!DOCTYPE html>
<html lang="en">
<head>
<meta charset="utf-8">
<title>Tasmer Business Cards</title>
<link href="https://fonts.googleapis.com/css2?family=Jost:wght@400;500;700&display=swap" rel="stylesheet">
<style>
  :root {
    --navy: #0455a3;
    --sky: #85acd3;
    --grey: #aaaaaa;
    --white: #ffffff;
    --backdrop: #e9edf2;
  }
  * { box-sizing: border-box; margin: 0; padding: 0; }
  html, body {
    width: 1200px; height: 900px; overflow: hidden;
    background: var(--backdrop);
    font-family: "Jost", "Futura", sans-serif;
  }
  .canvas { position: relative; width: 1200px; height: 900px; }
  .card {
    position: absolute; width: 700px; height: 400px;
    background: var(--sky); overflow: hidden;
    box-shadow: 0 10px 28px rgba(20, 40, 70, 0.22);
  }
  .card--front { left: 80px; top: 40px; }
  .card--back { left: 420px; top: 470px; }

  /* front */
  .portrait-art {
    position: absolute; left: 40px; top: 110px; width: 300px; height: 260px;
    background: var(--navy); border-radius: 46% 40% 44% 38% / 40% 46% 42% 48%;
  }
  .identity {
    position: absolute; left: 250px; top: 28px; color: var(--navy);
    line-height: 1.15;
  }
  .identity__title { font-size: 20px; font-weight: 500; }
  .identity__name { font-size: 24px; font-weight: 500; padding-left: 22px; }
  .contact-list { position: absolute; left: 370px; top: 104px; right: 0; list-style: none; }
  .contact-list__item {
    display: flex; align-items: center; gap: 14px;
    height: 48px; margin-bottom: 9px;
    background: var(--navy); color: var(--white);
    border-radius: 24px 0 0 24px;
    padding-left: 6px; font-size: 19px; line-height: 1.05;
  }
  .contact-list__item:nth-child(2) { margin-left: 22px; }
  .contact-list__item:nth-child(3) { margin-left: 44px; }
  .contact-list__item:nth-child(4) { margin-left: 66px; }
  .contact-list__item:nth-child(5) { margin-left: 88px; }
  .contact-icon {
    width: 36px; height: 36px; flex: none;
    border: 2px solid var(--white); border-radius: 50%;
    display: flex; align-items: center; justify-content: center;
  }
  .contact-icon svg { width: 20px; height: 20px; }

  /* back */
  .silhouette-art { position: absolute; inset: 0; }
  .brand {
    position: absolute; left: 0; right: 0; top: 132px;
    display: flex; flex-direction: column; align-items: center; color: var(--navy);
  }
  .brand__row { display: flex; align-items: center; gap: 16px; }
  .brand__dot { width: 58px; height: 58px; border-radius: 50%; background: var(--navy); }
  .brand__name { font-size: 92px; font-weight: 700; letter-spacing: 4px; line-height: 1; }
  .brand__tagline { font-size: 17px; font-weight: 500; letter-spacing: 5px; margin-top: 10px; }
</style>
</head>
<body>
<main class="canvas">

  <section class="card card--front" aria-label="Business card front">
    <div class="portrait-art" role="img" aria-label="Navy silhouette illustration of a dog's head"></div>

    <header class="identity">
      <p class="identity__title">Title</p>
      <p class="identity__name">Name and Surname</p>
    </header>

    <ul class="contact-list">
      <li class="contact-list__item">
        <span class="contact-icon"><svg viewBox="0 0 20 20" fill="none" stroke="#fff" stroke-width="1.6"><rect x="6" y="2" width="8" height="16" rx="1.5"/><line x1="9" y1="15" x2="11" y2="15"/></svg></span>
        mobile number
      </li>
      <li class="contact-list__item">
        <span class="contact-icon"><svg viewBox="0 0 20 20" fill="#fff"><path d="M5 2l3 3-1.6 2.2c1 2.2 2.6 3.8 4.6 4.8L13 10.4l3 3-2 3C8.5 16 3.5 11 3.5 4z"/></svg></span>
        officce number
      </li>
      <li class="contact-list__item">
        <span class="contact-icon"><svg viewBox="0 0 20 20" fill="none" stroke="#fff" stroke-width="1.6"><path d="M10 2l6 8-6 8-6-8z"/><path d="M4 10h12"/></svg></span>
        e-mail
      </li>
      <li class="contact-list__item">
        <span class="contact-icon"><svg viewBox="0 0 20 20" fill="none" stroke="#fff" stroke-width="1.4"><circle cx="10" cy="10" r="8"/><ellipse cx="10" cy="10" rx="3.5" ry="8"/><path d="M2 10h16M3.5 6h13M3.5 14h13"/></svg></span>
        web site
      </li>
      <li class="contact-list__item">
        <span class="contact-icon"><svg viewBox="0 0 20 20" fill="#fff"><path d="M10 1.5a6 6 0 0 0-6 6c0 4.5 6 11 6 11s6-6.5 6-11a6 6 0 0 0-6-6zm0 8.5a2.5 2.5 0 1 1 0-5 2.5 2.5 0 0 1 0 5z"/></svg></span>
        physical<br>address
      </li>
    </ul>
  </section>

  <section class="card card--back" aria-label="Business card back">
    <svg class="silhouette-art" viewBox="0 0 700 400" role="img" aria-label="Two large pale grey dog silhouette illustrations in opposite corners">
      <path d="M0 0 H250 C240 60 210 95 180 110 C130 125 90 110 60 140 C35 165 20 200 0 210 Z" fill="var(--grey)"/>
      <path d="M700 400 H420 C440 330 470 300 520 285 C570 270 600 290 630 250 C655 215 670 190 700 180 Z" fill="var(--grey)"/>
    </svg>

    <div class="brand">
      <div class="brand__row">
        <span class="brand__dot"></span>
        <span class="brand__name">TASMER</span>
      </div>
      <p class="brand__tagline">A CLOUD CONSULTING COMPANY</p>
    </div>
  </section>

</main>
</body>
</html>
```